KBT Business Cards

We require business cards for our business. We would like a matte black back to the card, with our logo centred in the middle. The front side of the card is open to design.

Target Market(s)

Clients looking for legal services (professional)

Industry/Entity Type

Legal

Contact Information for Business Card

Doran Kelbrath
Partner
Mobile: 0461 738 524
Email: doran@kbtlaw.co
Website: www.kbtlaw.co
Level 3, 118 Wendmore Street
Sydney NSW 2000

Font styles to use
Other font styles liked:
• Avenir

Colors
f04a50
ffffff
1b1b1b

Requirements
Must have
• Black back with logo included in the centre of the card.
• Our font is Avenir.

```html
<!DOCTYPE html>
<html lang="en">
<head>
<meta charset="utf-8">
<title>KBT Legal – Business Cards</title>
<link href="https://fonts.googleapis.com/css2?family=Nunito+Sans:wght@400;600;700&display=swap" rel="stylesheet">
<style>
  :root {
    --backdrop: #3a3a37;
    --card: #1b1b1b;
    --accent: #f04a50;
    --accent-deep: #c8264a;
    --ink: #ffffff;
    --ink-soft: #e6e6e6;
  }
  * { box-sizing: border-box; margin: 0; padding: 0; }
  html, body {
    width: 1200px; height: 824px; overflow: hidden;
    background: var(--backdrop);
    font-family: "Nunito Sans", "Avenir", sans-serif;
  }
  .stage {
    position: relative; width: 1200px; height: 824px;
    display: flex; align-items: center; justify-content: center; gap: 40px;
  }
  .card {
    position: relative; width: 540px; height: 330px;
    background: var(--card);
    box-shadow: 0 14px 30px rgba(0,0,0,.45);
    color: var(--ink);
  }
  .brand {
    display: flex; align-items: center; gap: 22px;
  }
  .brand-square {
    width: 58px; height: 58px; background: var(--accent-deep);
  }
  .brand-name {
    font-weight: 600; font-size: 34px; line-height: 1.02;
    letter-spacing: .5px; text-transform: uppercase; color: var(--ink);
  }
  /* back */
  .card-back { display: flex; align-items: center; justify-content: center; }
  /* front */
  .card-front .brand {
    position: absolute; left: 46px; top: 110px; gap: 16px;
  }
  .card-front .brand-square { width: 40px; height: 40px; }
  .card-front .brand-name { font-size: 22px; }
  .details {
    position: absolute; left: 262px; top: 88px;
  }
  .person-name {
    font-weight: 600; font-size: 25px; letter-spacing: .5px;
    text-transform: uppercase; line-height: 1.05;
  }
  .person-role {
    font-size: 14px; letter-spacing: 1.5px; color: var(--accent-deep);
    text-transform: uppercase; margin-bottom: 14px;
  }
  .contact-list { list-style: none; font-size: 14px; color: var(--ink-soft); }
  .contact-list li { display: flex; align-items: center; gap: 9px; margin-bottom: 5px; }
  .contact-list svg { width: 12px; height: 12px; flex: none; }
  .address { margin-top: 8px; font-size: 14px; line-height: 1.45; color: var(--ink-soft); }
</style>
</head>
<body>
<main class="stage">
  <section class="card card-back" aria-label="Card back">
    <div class="brand">
      <div class="brand-square"></div>
      <div class="brand-name">KBT<br>Legal</div>
    </div>
  </section>

  <section class="card card-front" aria-label="Card front">
    <div class="brand">
      <div class="brand-square"></div>
      <div class="brand-name">KBT<br>Legal</div>
    </div>
    <div class="details">
      <h1 class="person-name">Doran Kelbrath</h1>
      <p class="person-role">Partner</p>
      <ul class="contact-list">
        <li>
          <svg viewBox="0 0 12 12" aria-hidden="true"><rect x="3" y="0.8" width="6" height="10.4" rx="1" fill="none" stroke="var(--accent)" stroke-width="1.2"/><circle cx="6" cy="9.3" r=".7" fill="var(--accent)"/></svg>
          0461 738 524
        </li>
        <li>
          <svg viewBox="0 0 12 12" aria-hidden="true"><rect x="0.8" y="2.5" width="10.4" height="7" fill="var(--accent)"/><path d="M0.8 2.5 6 6.6 11.2 2.5" fill="none" stroke="var(--card)" stroke-width="1"/></svg>
          doran@kbtlaw.co
        </li>
        <li>
          <svg viewBox="0 0 12 12" aria-hidden="true"><g fill="none" stroke="var(--accent)" stroke-width="1"><circle cx="6" cy="6" r="5"/><ellipse cx="6" cy="6" rx="2.2" ry="5"/><path d="M1 6h10"/></g></svg>
          www.kbtlaw.co
        </li>
      </ul>
      <p class="address">Level 3, 118 Wendmore Street<br>Sydney NSW 2000</p>
    </div>
  </section>
</main>
</body>
</html>
```